Seeking funky, innovative business cards

I am looking to refresh our current business cards to something more engaging, visual and impactful. We are a management consultancy firm, see website (www.larkstone-partners.com.au). I've included our colour scheme, sample of the slides we use and our old business cards. We would like our cards to have icons. The card should display:- Name- Title- Mobile number- Address- Email address- Website - Company logo- Our purpose statement "We create the best places on earth to work"

Contact Information for Business Card

Brennan Ulfsson
Consultant
0468 927 341
Level 3, 218 Wexley Street, Melbourne 3000
brennan@larkstone-partners.com.au
www.larkstone-partners.com.au

Purpose statement "we create the best places on earth to work"
LOGO available in google images

Font styles to use
Other font styles liked:
• Open Sans Light, Bebas Neue (open to other cool foints)

Colors
ffc214
5c5c5c
f5f5f5
fefefe

Requirements
Must have
• - Name
• - Title
• - Mobile number
• - Address
• - Email address
• - Website
• - Company logo
• - Our purpose statement "We create the best places on earth to work"
Nice to have
• - Icons
• - Colour (see our colour scheme"

```html
<!DOCTYPE html>
<html lang="en">
<head>
<meta charset="utf-8">
<title>Larkstone Partners business cards</title>
<link rel="stylesheet" href="https://fonts.googleapis.com/css2?family=Montserrat:wght@500;600&family=Open+Sans:wght@300;400&display=swap">
<style>
  :root {
    --yellow: #ffc214;
    --orange: #f7a823;
    --charcoal: #474b4c;
    --grey-text: #5c5c5c;
    --paper: #fefefe;
    --backdrop: #e9e9e9;
  }
  * { box-sizing: border-box; margin: 0; padding: 0; }
  html, body { width: 1200px; height: 900px; overflow: hidden; }
  body {
    background: var(--backdrop);
    font-family: "Open Sans", Arial, sans-serif;
    position: relative;
  }
  .card {
    position: absolute;
    left: 250px;
    width: 700px;
    height: 400px;
    border-bottom: 9px solid var(--orange);
    box-shadow: 0 6px 18px rgba(0,0,0,0.18);
    overflow: hidden;
  }
  .card--front { top: 30px; background: var(--paper); }
  .card--back { top: 465px; background: var(--charcoal); }

  .brand {
    position: absolute;
    display: flex;
    align-items: center;
    gap: 10px;
    font-family: "Open Sans", Arial, sans-serif;
    font-weight: 300;
    white-space: nowrap;
  }
  .card--front .brand {
    top: 52px; right: 56px;
    font-size: 38px;
    color: var(--grey-text);
  }
  .brand__dot {
    width: 14px; height: 14px;
    border-radius: 50%;
    background: var(--yellow);
    flex: none;
  }
  .divider {
    position: absolute;
    left: 44px; right: 56px; top: 196px;
    height: 1.5px;
    background: var(--yellow);
  }
  .holder { position: absolute; left: 44px; top: 138px; }
  .holder__name {
    font-family: "Montserrat", Arial, sans-serif;
    font-weight: 600;
    font-size: 27px;
    letter-spacing: 1.5px;
    color: var(--yellow);
    text-transform: uppercase;
    line-height: 1.1;
  }
  .holder__title {
    font-size: 15px;
    color: var(--grey-text);
    margin-top: 2px;
  }
  .contacts {
    position: absolute;
    left: 44px; top: 222px;
    list-style: none;
    font-size: 15px;
    color: var(--grey-text);
  }
  .contacts li {
    display: flex;
    align-items: center;
    gap: 12px;
    line-height: 30px;
  }
  .contacts svg { width: 14px; height: 14px; fill: var(--orange); flex: none; }
  .address {
    position: absolute;
    right: 56px; bottom: 48px;
    text-align: right;
    font-size: 15px;
    line-height: 1.45;
    color: var(--grey-text);
    font-style: normal;
  }

  .card--back .brand {
    left: 0; right: 0; top: 130px;
    justify-content: center;
    font-size: 62px;
    color: #ffffff;
    gap: 16px;
  }
  .card--back .brand__dot { width: 20px; height: 20px; }
  .purpose {
    position: absolute;
    left: 0; right: 0; bottom: 56px;
    text-align: center;
    font-size: 22px;
    color: var(--yellow);
    letter-spacing: 0.5px;
  }
</style>
</head>
<body>
  <section class="card card--front" aria-label="Business card front">
    <div class="brand"><span class="brand__dot"></span>Larkstone Partners</div>
    <div class="holder">
      <p class="holder__name">Brennan Ulfsson</p>
      <p class="holder__title">Consultant</p>
    </div>
    <div class="divider"></div>
    <ul class="contacts">
      <li>
        <svg viewBox="0 0 24 24" aria-hidden="true"><path d="M6.6 10.8a15 15 0 0 0 6.6 6.6l2.2-2.2a1 1 0 0 1 1-.25 11.4 11.4 0 0 0 3.6.6 1 1 0 0 1 1 1V20a1 1 0 0 1-1 1A17 17 0 0 1 3 4a1 1 0 0 1 1-1h3.5a1 1 0 0 1 1 1c0 1.250.2 2.450.6 3.6a1 1 0 0 1-.25 1z"/></svg>
        + 61 3 9468 2730
      </li>
      <li>
        <svg viewBox="0 0 24 24" aria-hidden="true"><path d="M7 1h10a2 2 0 0 1 2 2v18a2 2 0 0 1-2 2H7a2 2 0 0 1-2-2V3a2 2 0 0 1 2-2zm0 3v14h10V4zm5 15.5a1.2 1.2 0 1 0 0 2.4 1.2 1.2 0 0 0 0-2.4z"/></svg>
        0468 927 341
      </li>
      <li>
        <svg viewBox="0 0 24 24" aria-hidden="true"><path d="M2 5h20v14H2zm2 2v.5l8 5 8-5V7zm0 2.8V17h16V9.8l-8 5z"/></svg>
        brennan@larkstone-partners.com.au
      </li>
      <li>
        <svg viewBox="0 0 24 24" aria-hidden="true"><path d="M12 2a10 10 0 1 0 0 20 10 10 0 0 0 0-20zm6.9 9h-3a15 15 0 0 0-1.3-5.6A8 8 0 0 1 18.9 11zM12 4.1c.9 1.3 1.8 3.7 1.9 6.9h-3.8c.1-3.2 1-5.6 1.9-6.9zM9.4 5.4A15 15 0 0 0 8.1 11h-3a8 8 0 0 1 4.3-5.6zM5.1 13h3a15 15 0 0 0 1.3 5.6A8 8 0 0 1 5.1 13zm6.9 6.9c-.9-1.3-1.8-3.7-1.9-6.9h3.8c-.1 3.2-1 5.6-1.9 6.9zm2.6-1.3a15 15 0 0 0 1.3-5.6h3a8 8 0 0 1-4.3 5.6z"/></svg>
        www.larkstone-partners.com.au
      </li>
    </ul>
    <address class="address">Level 3, 218 Wexley Street<br>Melbourne 3000</address>
  </section>

  <section class="card card--back" aria-label="Business card back">
    <div class="brand"><span class="brand__dot"></span>Larkstone Partners</div>
    <p class="purpose">We create the best places on earth to work</p>
  </section>
</body>
</html>
```